Professional & attention grabbing.

A business card design, front and back. I already have a logo I will attach, but I am open to something new as well.
Things to include:
Name:
Title:
Phone:
Email:
Wanting something that is professional but attention grabbing.
Also we do a lot of work using drones on natural gas pipelines (leading the future)if you want to include any of that. I'm open to ideas.
Target Market(s)
Natural gas transmission industry / greenhouse gas mitigation industry
Industry/Entity Type
Business
Colors
Designer to choose colors to be used in the design.
Look and feel
Each slider illustrates characteristics of the customer's brand and the style your logo design should communicate.

```html
<!DOCTYPE html>
<html lang="en">
<head>
<meta charset="UTF-8">
<title>KV Field Surveys – Business Card</title>
<link rel="stylesheet" href="https://fonts.googleapis.com/css2?family=Michroma&family=Roboto:wght@400;500;700&display=swap">
<style>
  :root {
    --page-bg: #d8d5d1;
    --card-bg: #eef0f0;
    --charcoal: #333335;
    --brand-red: #b3262b;
    --text-grey: #3d3d3f;
  }
  * { margin: 0; padding: 0; box-sizing: border-box; }
  html, body {
    width: 1200px;
    height: 1010px;
    overflow: hidden;
    background: var(--page-bg);
  }
  .card {
    position: absolute;
    left: 100px;
    top: 217px;
    width: 1000px;
    height: 576px;
    background: var(--card-bg);
    box-shadow: 0 10px 30px rgba(0,0,0,0.18);
    font-family: "Roboto", Arial, sans-serif;
    color: var(--text-grey);
  }
  .side-band {
    position: absolute;
    left: 0; top: 0;
    width: 85px; height: 100%;
    background: var(--charcoal);
  }
  .side-stripe {
    position: absolute;
    left: 85px; top: 0;
    width: 10px; height: 100%;
    background: var(--brand-red);
  }
  .brand {
    position: absolute;
    right: 68px;
    top: 62px;
    display: flex;
    align-items: center;
    gap: 16px;
  }
  .brand-square {
    width: 56px; height: 56px;
    background: var(--brand-red);
  }
  .brand-name {
    font-family: "Roboto", Arial, sans-serif;
    font-weight: 700;
    font-size: 40px;
    letter-spacing: 0.5px;
    color: var(--charcoal);
    line-height: 1;
  }
  .person {
    position: absolute;
    left: 132px;
    top: 312px;
  }
  .person-name {
    font-family: "Michroma", "Arial Black", sans-serif;
    font-size: 28px;
    font-weight: 400;
    color: var(--brand-red);
    letter-spacing: 1px;
    -webkit-text-stroke: 0.8px var(--brand-red);
  }
  .person-title {
    margin-top: 10px;
    font-size: 21px;
    color: var(--text-grey);
  }
  .contacts {
    position: absolute;
    left: 132px;
    top: 434px;
    list-style: none;
  }
  .contact-item {
    display: flex;
    align-items: center;
    gap: 16px;
    height: 33.5px;
    font-size: 22px;
    color: var(--text-grey);
  }
  .contact-icon { width: 22px; height: 22px; fill: var(--brand-red); flex: none; }
</style>
</head>
<body>
  <section class="card" aria-label="Business card front">
    <div class="side-band"></div>
    <div class="side-stripe"></div>

    <div class="brand">
      <div class="brand-square"></div>
      <span class="brand-name">KV Field Surveys</span>
    </div>

    <div class="person">
      <h1 class="person-name">DANIEL REYES</h1>
      <p class="person-title">Managing Director</p>
    </div>

    <ul class="contacts">
      <li class="contact-item">
        <svg class="contact-icon" viewBox="0 0 24 24" aria-hidden="true">
          <path d="M3 8c0-2 4-4 9-4s9 2 9 4v2h-5V8.5c-1.5-.5-6.5-.5-8 0V10H3z"/>
          <path d="M6 11h12l2 9H4z M9 13.5a3 3 0 1 0 6 0a3 3 0 1 0-6 0z" fill-rule="evenodd"/>
        </svg>
        <span>1300 418 552</span>
      </li>
      <li class="contact-item">
        <svg class="contact-icon" viewBox="0 0 24 24" aria-hidden="true">
          <path d="M12 2a10 10 0 1 0 0 20a10 10 0 1 0 0-20zm0 2c1.2 1.3 2 3.7 2.2 7H9.8C10 7.7 10.8 5.3 12 4zM8 11H4.1A8 8 0 0 1 9.3 4.5C8.5 6.2 8.1 8.4 8 11zm0 2c.1 2.6.5 4.8 1.3 6.5A8 8 0 0 1 4.1 13zm1.8 0h4.4c-.2 3.3-1 5.7-2.2 7c-1.2-1.3-2-3.7-2.2-7zm6.2 0h3.9a8 8 0 0 1-5.2 6.5c.8-1.7 1.2-3.9 1.3-6.5zm0-2c-.1-2.6-.5-4.8-1.3-6.5A8 8 0 0 1 19.9 11z"/>
        </svg>
        <span>www.kvfieldsurveys.com</span>
      </li>
      <li class="contact-item">
        <svg class="contact-icon" viewBox="0 0 24 24" aria-hidden="true">
          <path d="M2 5h20v14H2z M4 7v.5l8 6l8-6V7z" fill-rule="evenodd"/>
        </svg>
        <span>daniel.reyes@kvfieldsurveys.com</span>
      </li>
    </ul>
  </section>
</body>
</html>
```